Exciting & Elegant Stationary Pack

Stationary consists of
1. Letter head / Envelope
2. Business Card
3. Invoice
4. 40x40mm sticker

Attached files;

1. Logo (Other formats available on request)
2. MS word Doc - For information and description of design
3. Website image (This will be our new website so use the colours so everything ties together)
4. Sample of stationary pack we like, but feel free to be creative

Target Market(s)

Home improvement

Industry/Entity Type

Construction

Font styles to use
Other font styles liked:
• Leave up to designer - We like font used on (website attached image)

Requirements
Must have
• Please look at uploaded file of sample website and use colours
Nice to have
• Any type of business card design - eg. metal, die cut, embossed, etc...

```html
<!DOCTYPE html>
<html lang="en">
<head>
<meta charset="utf-8">
<title>Setline Tiling – Business Card</title>
<link rel="stylesheet" href="https://fonts.googleapis.com/css2?family=Archivo:wght@400;700;800&display=swap">
<style>
  :root {
    --stage: #2b2b2d;
    --navy: #0f3f63;
    --white: #ffffff;
    --paper: #f4f4f2;
    --orange: #f08b3e;
    --orange-deep: #c9692a;
    --ink-soft: #d9e2ea;
  }
  * { box-sizing: border-box; margin: 0; padding: 0; }
  html, body { width: 1200px; height: 950px; overflow: hidden; }
  body {
    background: var(--stage);
    font-family: "Archivo", Arial, sans-serif;
    display: flex;
    flex-direction: column;
    align-items: center;
    justify-content: center;
    gap: 48px;
  }
  .card {
    position: relative;
    width: 660px;
    height: 403px;
    overflow: hidden;
    box-shadow: 0 10px 30px rgba(0,0,0,.45);
  }
  .card-bg { position: absolute; inset: 0; width: 100%; height: 100%; }

  /* back */
  .card-back { background: linear-gradient(135deg, var(--orange) 0%, var(--orange-deep) 100%); }
  .back-brand {
    position: absolute;
    left: 352px;
    top: 208px;
    width: 260px;
    font-weight: 800;
    font-size: 28px;
    letter-spacing: 1px;
    line-height: 1;
    white-space: nowrap;
    color: var(--white);
  }

  /* front */
  .card-front { background: var(--white); }
  .front-brand {
    position: absolute;
    left: 34px;
    top: 20px;
    font-weight: 800;
    font-size: 60px;
    letter-spacing: 2px;
    line-height: 1;
    white-space: nowrap;
    color: var(--navy);
  }
  .contact {
    position: absolute;
    left: 34px;
    top: 196px;
    list-style: none;
    color: var(--white);
    font-size: 15px;
    line-height: 1.6;
  }
  .contact li { display: flex; align-items: center; gap: 10px; }
  .contact .licence { margin-bottom: 4px; }
  .contact svg { width: 14px; height: 14px; flex: none; }
  .person {
    position: absolute;
    left: 402px;
    bottom: 36px;
    color: var(--ink-soft);
  }
  .person-name { font-weight: 700; font-size: 18px; letter-spacing: .5px; }
  .person-role { font-size: 16px; letter-spacing: .5px; }
</style>
</head>
<body>

  <section class="card card-back">
    <svg class="card-bg" viewBox="0 0 660 403" preserveAspectRatio="none">
      <polygon points="350,250 560,250 660,330 660,403 470,403" fill="var(--navy)"/>
    </svg>
    <div class="back-brand">SETLINE TILING</div>
  </section>

  <section class="card card-front">
    <svg class="card-bg" viewBox="0 0 660 403" preserveAspectRatio="none">
      <polygon points="0,92 470,92 660,300 660,403 0,403" fill="var(--navy)"/>
      <polygon points="470,92 660,92 660,300" fill="var(--paper)"/>
    </svg>
    <div class="front-brand">SETLINE TILING</div>

    <ul class="contact">
      <li class="licence">Lic No. 204519c</li>
      <li>
        <svg viewBox="0 0 14 14"><rect x="3" y="0.5" width="8" height="13" rx="1.5" fill="none" stroke="currentColor" stroke-width="1.4"/><circle cx="7" cy="11" r="0.9" fill="currentColor"/></svg>
        0400 318 752
      </li>
      <li>
        <svg viewBox="0 0 14 14"><rect x="0.7" y="2.5" width="12.6" height="9" fill="none" stroke="currentColor" stroke-width="1.4"/><polyline points="0.7,2.5 7,8 13.3,2.5" fill="none" stroke="currentColor" stroke-width="1.4"/></svg>
        info@setlinetiling.com.au
      </li>
      <li>
        <svg viewBox="0 0 14 14"><circle cx="7" cy="7" r="6" fill="none" stroke="currentColor" stroke-width="1.4"/><ellipse cx="7" cy="7" rx="2.5" ry="6" fill="none" stroke="currentColor" stroke-width="1.2"/><line x1="1" y1="7" x2="13" y2="7" stroke="currentColor" stroke-width="1.2"/></svg>
        www.setlinetiling.com.au
      </li>
    </ul>

    <div class="person">
      <div class="person-name">MARA ELLISON</div>
      <div class="person-role">PROJECT MANAGER</div>
    </div>
  </section>

</body>
</html>
```